FinTech company looking to revamp and expand client-facing interface for our financial models

Pellworth Engines currently has a very simple website that allows clients to interact with our financial models. We are looking to completely redesign the current site and add several extra pages to provide extra functionality. We want the design to have a modern, slick feel, that will work on both a desktop or a tablet. It should be straightforward for clients to move between different pages at any time, and clear from the layout how to interact with the more advanced features. We have included screenshots of existing pages in the attached design brief, as well as sketches of the functionality required by the new pages, but can't provide a direct link to the current site.
Target Market(s)
Professional investors that will be paying to access the interface
Industry/Entity Type
Finance
Number of Pages Required
4 page
Colors
Designer to choose colors to be used in the design.
Look and feel
Each slider illustrates characteristics of the customer's brand and the style your logo design should communicate.

```html
<!DOCTYPE html>
<html lang="en">
<head>
<meta charset="utf-8">
<title>Pellworth Engines – Model Interface</title>
<link href="https://fonts.googleapis.com/css2?family=Oswald:wght@400&family=Roboto:wght@400;500&display=swap" rel="stylesheet">
<style>
:root{
  --page-bg:#b7bac3;
  --brand:#0066ff;
  --brand-active:#0052cc;
  --rule:#333538;
  --panel:#f2f3f7;
  --head:#333333;
  --row-a:#e2e4ea;
  --row-b:#eef0f4;
  --text:#333;
  --input-border:#c8cad0;
  --button:#555759;
}
*{box-sizing:border-box;margin:0;padding:0}
html,body{width:809px;height:1200px;overflow:hidden}
body{background:var(--page-bg);font-family:"Roboto",sans-serif;color:var(--text);position:relative}
.screen{position:absolute;left:33px;width:746px}
.topbar{height:36px;background:var(--brand);border-bottom:2px solid var(--rule);position:relative;color:#fff}
.brand{position:absolute;left:13px;top:5px;font-family:"Oswald",sans-serif;font-size:20px;letter-spacing:.2px;line-height:26px}
.nav-item{position:absolute;top:7px;height:22px;line-height:22px;font-size:9px;font-weight:500;letter-spacing:.2px;text-align:center;display:flex;align-items:center;justify-content:center;gap:4px}
.nav-item.active{background:var(--brand-active);border-radius:2px}
.nav-item svg{width:8px;height:8px;fill:#fff}
.dropdown{position:absolute;left:481px;top:29px;width:67px;background:var(--panel);border-radius:0 0 3px 3px;box-shadow:0 1px 2px rgba(0,0,0,.15);z-index:2}
.dropdown div{height:18px;line-height:18px;font-size:7px;text-align:right;padding-right:10px;border-bottom:1px solid #e0e2e7;color:#444}
.dropdown div.current{color:var(--brand)}
.dropdown div:last-child{border-bottom:none}
.panel{height:287px;background:var(--panel);position:relative}
.filter{position:absolute;left:13px;display:flex;align-items:center}
.filter .small{font-size:7px;width:49px}
.filter .big{font-size:13.5px;font-weight:500;color:#333}
.filter .abs{font-size:13.5px;font-weight:500;width:49px;position:relative}
.filter .abs sup{font-size:6.5px;font-weight:400;position:absolute;left:30px;top:-1px}
.field{width:130px;height:18px;border:1px solid var(--input-border);background:#fff;border-radius:2px;font-size:7px;line-height:16px;padding-left:8px}
.filter .big+.field{margin-left:10px}
.stat-filter{position:absolute;left:13px;display:flex;align-items:center}
.stat-filter label{font-size:7px;width:60px}
.export{position:absolute;right:13px;top:13px;width:49px;height:18px;background:var(--button);color:#fff;border-radius:2px;font-size:7px;display:flex;align-items:center;justify-content:center;gap:3px}
.export svg{width:7px;height:7px;fill:none;stroke:#fff;stroke-width:1.5}
.grid{position:absolute;left:13px;width:719px;border-collapse:collapse;table-layout:fixed;font-size:7px}
.grid th{background:var(--head);color:#fff;font-weight:400;height:27px;text-align:left;padding-left:7px;border-right:1px solid #444}
.grid th:last-child,.grid td:last-child{border-right:none}
.grid td{height:28px;padding-left:7px;border-right:1px solid #fff;border-top:2px solid var(--panel);line-height:9px;vertical-align:middle}
.grid tbody tr:nth-child(odd) td{background:var(--row-a)}
.grid tbody tr:nth-child(even) td{background:var(--row-b)}
.grid td.top{vertical-align:top;padding-top:7px}
.grid td.id{padding-left:13px}
.caret{display:inline-block;border-left:2.5px solid transparent;border-right:2.5px solid transparent;border-top:3px solid #fff;margin-left:4px;vertical-align:middle}
.legal{position:absolute;left:0;width:746px;text-align:center;font-size:7px;color:#333}
</style>
</head>
<body>

<!-- Equities view -->
<section class="screen" style="top:36px">
  <header class="topbar">
    <div class="brand">PELLWORTH</div>
    <div class="nav-item" style="left:209px;width:46px">250D</div>
    <div class="nav-item" style="left:272px;width:46px">83D</div>
    <div class="nav-item" style="left:332px;width:46px">42D</div>
    <div class="nav-item active" style="left:481px;width:67px"><svg viewBox="0 0 10 10"><path d="M5 1 0.5 5H2v4h2.3V6.5h1.4V9H8V5h1.5z"/></svg>MODELS</div>
    <div class="nav-item" style="left:571px;width:71px"><svg viewBox="0 0 10 10"><circle cx="5" cy="5" r="3.2"/><path d="M5 0v10M0 5h10M1.5 1.5l7 7M8.5 1.5l-7 7" stroke="#fff" stroke-width="1.4"/></svg>SENSITIVITIES</div>
    <div class="nav-item" style="left:675px;width:57px"><svg viewBox="0 0 10 10"><path d="M5 .5l1.4 3 3.2.3-2.4 2.1.8 3.2L5 7.4 2 9.1l.8-3.2L.4 3.8l3.2-.3z"/></svg>FAVOURITE</div>
  </header>
  <div class="panel">
    <div class="filter" style="top:13px"><span class="small">Quality</span><span class="big">Threshold</span><div class="field">- 10</div></div>
    <div class="filter" style="top:40px"><span class="abs">Abs.<sup>Stat</sup></span><span class="big">Threshold</span><div class="field">- 10</div></div>
    <div class="export"><svg viewBox="0 0 8 8"><path d="M6 4.5V7H1V2h2.5M4.5 1H7v2.5M7 1 3.5 4.5"/></svg>EXPORT</div>
    <table class="grid" style="top:76px">
      <colgroup><col style="width:50px"><col style="width:77px"><col style="width:67px"><col style="width:68px"><col style="width:57px"><col style="width:57px"><col style="width:57px"><col style="width:57px"><col style="width:57px"><col style="width:57px"><col style="width:57px"><col style="width:57px"></colgroup>
      <thead><tr><th style="padding-left:13px">ID<span class="caret"></span></th><th>Sector</th><th>Time</th><th>Quality</th><th>Stat 1</th><th>Stat 2</th><th>Stat 3</th><th>Stat 4</th><th>Stat 5</th><th>Stat 6</th><th>Stat 7</th><th>Stat 8</th></tr></thead>
      <tbody>
        <tr><td class="id">Model 1</td><td>Materials</td><td>2019-07-03<br>12:15:00.000</td><td>30.2288</td><td>2.01577</td><td>23.305</td><td>-0.149368</td><td>22.3054</td><td>4.63714</td><td>0.945706</td><td>2.81949</td><td>2.60858</td></tr>
        <tr><td class="id">Model 2</td><td>Industrials</td><td>2019-07-03<br>12:15:00.000</td><td>32.8694</td><td>0.87307</td><td>32.185</td><td>-0.0336927</td><td>33.9944</td><td>11.5969</td><td>-0.750396</td><td>0.449595</td><td>4.69146</td></tr>
        <tr><td class="id">Model 3</td><td>Consumer<br>Discretionary</td><td>2019-07-03<br>12:15:00.000</td><td>1.66002</td><td>-0.56922</td><td>159.814</td><td>0.0252328</td><td>172.616</td><td>10.2845</td><td>-0.472968</td><td>-0.830458</td><td>6.80646</td></tr>
        <tr><td class="id">Model 4</td><td>Information<br>Technology</td><td>2019-07-03<br>12:15:00.000</td><td>45.6856</td><td>0.412148</td><td>202.488</td><td>0.00849232</td><td>205.834</td><td>11.9094</td><td>-0.750396</td><td>-0.385309</td><td>4.69146</td></tr>
        <tr><td class="id">Model 5</td><td>Information<br>Technology</td><td>2019-07-03<br>12:15:00.000</td><td>75.1133</td><td>7.06728</td><td>188.605</td><td>0.016913</td><td>181.655</td><td>3.82241</td><td>-0.137913</td><td>0.449595</td><td>3.85120</td></tr>
        <tr><td class="id">Model 6</td><td>Information<br>Technology</td><td>2019-07-03<br>12:15:00.000</td><td>75.7733</td><td>0.412148</td><td>23.305</td><td>0.0252328</td><td>22.3054</td><td>4.66458</td><td>0.981019</td><td>1.29847</td><td>3.349277</td></tr>
      </tbody>
    </table>
  </div>
  <p class="legal" style="top:333px">Copyright © 2019 Pellworth. All rights reserved.</p>
</section>

<!-- Equities view with models menu open -->
<section class="screen" style="top:400px">
  <header class="topbar">
    <div class="brand">PELLWORTH</div>
    <div class="nav-item" style="left:209px;width:46px">250D</div>
    <div class="nav-item" style="left:272px;width:46px">83D</div>
    <div class="nav-item" style="left:332px;width:46px">42D</div>
    <div class="nav-item active" style="left:481px;width:67px"><svg viewBox="0 0 10 10"><path d="M5 1 0.5 5H2v4h2.3V6.5h1.4V9H8V5h1.5z"/></svg>MODELS</div>
    <div class="nav-item" style="left:571px;width:71px"><svg viewBox="0 0 10 10"><circle cx="5" cy="5" r="3.2"/><path d="M5 0v10M0 5h10M1.5 1.5l7 7M8.5 1.5l-7 7" stroke="#fff" stroke-width="1.4"/></svg>SENSITIVITIES</div>
    <div class="nav-item" style="left:675px;width:57px"><svg viewBox="0 0 10 10"><path d="M5 .5l1.4 3 3.2.3-2.4 2.1.8 3.2L5 7.4 2 9.1l.8-3.2L.4 3.8l3.2-.3z"/></svg>FAVOURITE</div>
    <nav class="dropdown"><div class="current">EQUITIES</div><div>ETFS</div><div>PAIRS</div><div>ETF PAIRS</div><div>FACTORS</div></nav>
  </header>
  <div class="panel">
    <div class="filter" style="top:13px"><span class="small">Quality</span><span class="big">Threshold</span><div class="field">- 10</div></div>
    <div class="filter" style="top:40px"><span class="abs">Abs.<sup>Stat</sup></span><span class="big">Threshold</span><div class="field">- 10</div></div>
    <div class="export"><svg viewBox="0 0 8 8"><path d="M6 4.5V7H1V2h2.5M4.5 1H7v2.5M7 1 3.5 4.5"/></svg>EXPORT</div>
    <table class="grid" style="top:76px">
      <colgroup><col style="width:50px"><col style="width:77px"><col style="width:67px"><col style="width:68px"><col style="width:57px"><col style="width:57px"><col style="width:57px"><col style="width:57px"><col style="width:57px"><col style="width:57px"><col style="width:57px"><col style="width:57px"></colgroup>
      <thead><tr><th style="padding-left:13px">ID<span class="caret"></span></th><th>Sector</th><th>Time</th><th>Quality</th><th>Stat 1</th><th>Stat 2</th><th>Stat 3</th><th>Stat 4</th><th>Stat 5</th><th>Stat 6</th><th>Stat 7</th><th>Stat 8</th></tr></thead>
      <tbody>
        <tr><td class="id">Model 1</td><td>Materials</td><td>2019-07-03<br>12:15:00.000</td><td>30.2288</td><td>2.01577</td><td>23.305</td><td>-0.149368</td><td>22.3054</td><td>4.63714</td><td>0.945706</td><td>2.81949</td><td>2.60858</td></tr>
        <tr><td class="id">Model 2</td><td>Industrials</td><td>2019-07-03<br>12:15:00.000</td><td>32.8694</td><td>0.87307</td><td>32.185</td><td>-0.0336927</td><td>33.9944</td><td>11.5969</td><td>-0.750396</td><td>0.449595</td><td>4.69146</td></tr>
        <tr><td class="id">Model 3</td><td>Consumer<br>Discretionary</td><td>2019-07-03<br>12:15:00.000</td><td>1.66002</td><td>-0.56922</td><td>159.814</td><td>0.0252328</td><td>172.616</td><td>10.2845</td><td>-0.472968</td><td>-0.830458</td><td>6.80646</td></tr>
        <tr><td class="id">Model 4</td><td>Information<br>Technology</td><td>2019-07-03<br>12:15:00.000</td><td>45.6856</td><td>0.412148</td><td>202.488</td><td>0.00849232</td><td>205.834</td><td>11.9094</td><td>-0.750396</td><td>-0.385309</td><td>4.69146</td></tr>
        <tr><td class="id">Model 5</td><td>Information<br>Technology</td><td>2019-07-03<br>12:15:00.000</td><td>75.1133</td><td>7.06728</td><td>188.605</td><td>0.016913</td><td>181.655</td><td>3.82241</td><td>-0.137913</td><td>0.449595</td><td>3.85120</td></tr>
        <tr><td class="id">Model 6</td><td>Information<br>Technology</td><td>2019-07-03<br>12:15:00.000</td><td>75.7733</td><td>0.412148</td><td>23.305</td><td>0.0252328</td><td>22.3054</td><td>4.66458</td><td>0.981019</td><td>1.29847</td><td>3.349277</td></tr>
      </tbody>
    </table>
  </div>
  <p class="legal" style="top:333px">Copyright © 2019 Pellworth. All rights reserved.</p>
</section>

<!-- 250D factor view -->
<section class="screen" style="top:819px">
  <header class="topbar">
    <div class="brand">PELLWORTH</div>
    <div class="nav-item active" style="left:198px;width:67px">250D</div>
    <div class="nav-item" style="left:272px;width:46px">83D</div>
    <div class="nav-item" style="left:332px;width:46px">42D</div>
    <div class="nav-item" style="left:481px;width:67px"><svg viewBox="0 0 10 10"><path d="M5 1 0.5 5H2v4h2.3V6.5h1.4V9H8V5h1.5z"/></svg>MODELS</div>
    <div class="nav-item" style="left:571px;width:71px"><svg viewBox="0 0 10 10"><circle cx="5" cy="5" r="3.2"/><path d="M5 0v10M0 5h10M1.5 1.5l7 7M8.5 1.5l-7 7" stroke="#fff" stroke-width="1.4"/></svg>SENSITIVITIES</div>
    <div class="nav-item" style="left:675px;width:57px"><svg viewBox="0 0 10 10"><path d="M5 .5l1.4 3 3.2.3-2.4 2.1.8 3.2L5 7.4 2 9.1l.8-3.2L.4 3.8l3.2-.3z"/></svg>FAVOURITE</div>
  </header>
  <div class="panel">
    <div class="stat-filter" style="top:13px"><label>Stat 1 Threshold</label><div class="field">- 10</div></div>
    <div class="stat-filter" style="top:36px"><label>Stat 2 Threshold</label><div class="field">- 10</div></div>
    <div class="stat-filter" style="top:58px"><label>Stat 3 Threshold</label><div class="field">- 10</div></div>
    <div class="export"><svg viewBox="0 0 8 8"><path d="M6 4.5V7H1V2h2.5M4.5 1H7v2.5M7 1 3.5 4.5"/></svg>EXPORT</div>
    <table class="grid" style="top:90px">
      <colgroup><col style="width:68px"><col style="width:59px"><col style="width:135px"><col style="width:83px"><col style="width:81px"><col style="width:80px"><col style="width:82px"><col style="width:81px"><col style="width:50px"></colgroup>
      <thead><tr><th style="padding-left:9px">Factor</th><th>ID<span class="caret"></span></th><th style="padding-left:9px">Sector</th><th>Stat 1</th><th>Stat 2</th><th>Stat 3</th><th>Stat 4</th><th>Stat 5</th><th>Stat 6</th></tr></thead>
      <tbody>
        <tr><td class="top" style="padding-left:9px">Factor 1</td><td>Model 1</td><td style="padding-left:9px">Materials</td><td>-1.4</td><td>0.1</td><td>-3.1</td><td>0.7</td><td>30.2</td><td>0.9</td></tr>
        <tr><td class="top" style="padding-left:9px">Factor 2</td><td>Model 2</td><td style="padding-left:9px">Industrials</td><td>2.8</td><td>0.6</td><td>6.1</td><td>100</td><td>30.2</td><td>0.9</td></tr>
        <tr><td class="top" style="padding-left:9px">Factor 3</td><td>Model 3</td><td style="padding-left:9px">Consumer<br>Discretionary</td><td>-3.7</td><td>2.7</td><td>-7.2</td><td>100</td><td>30.2</td><td>0.9</td></tr>
        <tr><td class="top" style="padding-left:9px">Factor 1</td><td>Model 4</td><td style="padding-left:9px">Information<br>Technology</td><td>2.8</td><td>0.2</td><td>2.7</td><td>0.5</td><td>32.9</td><td>-0.5</td></tr>
        <tr><td class="top" style="padding-left:9px">Factor 2</td><td>Model 5</td><td style="padding-left:9px">Information<br>Technology</td><td>0.8</td><td>0.3</td><td>2.5</td><td>0.5</td><td>32.9</td><td>-0.5</td></tr>
        <tr><td class="top" style="padding-left:9px">Factor 3</td><td>Model 6</td><td style="padding-left:9px">Information<br>Technology</td><td>-3.4</td><td>0.7</td><td>2.8</td><td>0.9</td><td>32.9</td><td>-0.5</td></tr>
      </tbody>
    </table>
  </div>
  <p class="legal" style="top:333px">Copyright © 2019 Pellworth. All rights reserved.</p>
</section>

</body>
</html>
```